Redesign of business card for Cedar Ridge Mechanical

We are looking for a new design for our business cards for Cedar Ridge Mechanical. We are a plumbing & HVAC construction company, operating on the West Coast of Canada and USA. Logo attached.
Industry/Entity Type
Construction - Plumbing & HVAC
Contact Information for Business Card
Name, address, phone numbers, email, website address
Look and feel
Each slider illustrates characteristics of the customer's brand and the style your logo design should communicate.

```html
<!DOCTYPE html>
<html lang="en">
<head>
<meta charset="utf-8">
<title>Cedar Ridge Mechanical – Business Card</title>
<link href="https://fonts.googleapis.com/css2?family=Montserrat:wght@400;700&family=Oswald:wght@500&display=swap" rel="stylesheet">
<style>
  :root {
    --bg: #6e6e6e;
    --bg-edge: #565656;
    --card: #151515;
    --card-edge: #b9b9b9;
    --silver: #d6d6d6;
    --silver-soft: #a8a8a8;
    --rule: #8a8a8a;
  }
  * { box-sizing: border-box; margin: 0; padding: 0; }
  html, body { width: 1200px; height: 800px; overflow: hidden; }
  body {
    background: radial-gradient(ellipse at 50% 40%, var(--bg) 0%, var(--bg-edge) 100%);
    font-family: "Montserrat", sans-serif;
    display: flex;
    align-items: center;
    justify-content: center;
    gap: 40px;
  }
  .card {
    position: relative;
    width: 540px;
    height: 309px;
    background: var(--card);
    border-radius: 22px;
    box-shadow: 0 0 0 1.5px var(--card-edge), 0 18px 30px rgba(0,0,0,.45);
    color: var(--silver);
    overflow: hidden;
  }

  /* Front */
  .brand-mark {
    position: absolute;
    top: 42px;
    right: 34px;
    display: flex;
    align-items: center;
    gap: 10px;
    font-family: "Oswald", sans-serif;
    font-weight: 500;
    font-size: 17px;
    letter-spacing: 1.5px;
    text-transform: uppercase;
    color: var(--silver);
  }
  .brand-mark .square {
    width: 14px; height: 14px;
    border: 2px solid var(--silver);
    border-radius: 3px;
  }
  .holder {
    position: absolute;
    left: 34px;
    top: 88px;
  }
  .holder .name {
    font-weight: 700;
    font-size: 19px;
    letter-spacing: .5px;
    text-transform: uppercase;
    color: var(--silver);
  }
  .holder .title {
    font-size: 13px;
    color: var(--silver-soft);
    margin-top: 2px;
  }
  .divider {
    position: absolute;
    left: 34px;
    right: 34px;
    top: 150px;
    height: 1px;
    background: var(--rule);
  }
  .contacts {
    position: absolute;
    left: 34px;
    top: 166px;
    list-style: none;
    font-size: 13px;
    line-height: 24px;
    color: var(--silver);
  }
  .contacts li { display: flex; align-items: center; gap: 10px; }
  .contacts svg { width: 12px; height: 12px; fill: var(--silver); flex: none; }
  .address {
    position: absolute;
    right: 34px;
    top: 170px;
    text-align: right;
    font-size: 13px;
    line-height: 22px;
    color: var(--silver-soft);
    font-style: normal;
  }

  /* Back */
  .card--back { display: flex; align-items: center; justify-content: center; }
  .back-name {
    font-family: "Oswald", sans-serif;
    font-weight: 500;
    font-size: 34px;
    letter-spacing: 3px;
    text-transform: uppercase;
    color: var(--silver);
  }
</style>
</head>
<body>

<section class="card card--front">
  <div class="brand-mark"><span class="square"></span>Cedar Ridge Mechanical</div>

  <div class="holder">
    <p class="name">Martin Caldwell</p>
    <p class="title">President</p>
  </div>

  <div class="divider"></div>

  <ul class="contacts">
    <li>
      <svg viewBox="0 0 24 24" aria-hidden="true"><path d="M6.6 10.8a15.1 15.1 0 0 0 6.6 6.6l2.2-2.2a1 1 0 0 1 1-.25 11.4 11.4 0 0 0 3.6.57 1 1 0 0 1 1 1V20a1 1 0 0 1-1 1A17 17 0 0 1 3 4a1 1 0 0 1 1-1h3.5a1 1 0 0 1 1 1c0 1.25.2 2.45.57 3.57a1 1 0 0 1-.25 1z"/></svg>
      1-866-555-0142 Toll Free
    </li>
    <li>
      <svg viewBox="0 0 24 24" aria-hidden="true"><path d="M6.6 10.8a15.1 15.1 0 0 0 6.6 6.6l2.2-2.2a1 1 0 0 1 1-.25 11.4 11.4 0 0 0 3.6.57 1 1 0 0 1 1 1V20a1 1 0 0 1-1 1A17 17 0 0 1 3 4a1 1 0 0 1 1-1h3.5a1 1 0 0 1 1 1c0 1.25.2 2.45.57 3.57a1 1 0 0 1-.25 1z"/></svg>
      213-555-0187
    </li>
    <li>
      <svg viewBox="0 0 24 24" aria-hidden="true"><path d="M2 5h20v14H2zm2 2v.5l8 5 8-5V7l-8 5z"/></svg>
      info@cedarridgemech.com
    </li>
    <li>
      <svg viewBox="0 0 24 24" aria-hidden="true"><path d="M12 2a10 10 0 1 0 0 20 10 10 0 0 0 0-20zm0 2c.9 0 2.2 1.8 2.8 5H9.2C9.8 5.8 11.1 4 12 4zM4.3 11h4.8a17 17 0 0 0 0 2H4.3a8 8 0 0 1 0-2zm10.6 0h4.8a8 8 0 0 1 0 2h-4.8a17 17 0 0 0 0-2zM9.2 15h5.6c-.6 3.2-1.9 5-2.8 5s-2.2-1.8-2.8-5z"/></svg>
      www.cedarridgemech.com
    </li>
  </ul>

  <address class="address">
    4150 Harbor Lane<br>
    Suite 200, Fairview, CA 92701
  </address>
</section>

<section class="card card--back">
  <p class="back-name">Cedar Ridge Mechanical</p>
</section>

</body>
</html>
```